Retail Product Label Design

We need a 4" w X 3" h label. The label will be applied to a stand up zip lock clear poly bag. 2" at the bottom of the bag will remain clear as a window to the product. The product is small packs of minerals that are placed in fruit, vegetable and flower storage. please go to www.sackpalo.com for more info. We are thinking a green color with fruits and vegetables included similar to what we use now (see attached file). We would like to consider a retro-style (bright colors almost cartoonish like the labels on TK's Alehall Beer Labels and glasses. We have exact specs for the layout when necessary. They can be found @ http://www.wrapcratemart.com/images/main/wcm-label-requirements.pdf. We would also like to freshen up our logo (see attached file). This will be one of possibly 3 labels. One label will focus on fruits and vegetables, one will focus on flowers and one will focus on valuables like electronics, cameras and silver jewelry. Colors should be limited to 5 or possibly 6.
Target Market(s)
Grocery store fruit and vegetable buyers
Industry/Entity Type
Electronics
Look and feel
Each slider illustrates characteristics of the customer's brand and the style your logo design should communicate.

```html
<!DOCTYPE html>
<html lang="en">
<head>
<meta charset="utf-8">
<title>SackPalo – Keep Produce Fresher Longer</title>
<link rel="stylesheet" href="https://fonts.googleapis.com/css2?family=Russo+One&family=Cinzel:wght@700&display=swap">
<style>
  :root {
    --page: #ffffff;
    --frame: #c9d9cc;
    --green-bright: #3fb04a;
    --green-mid: #1f8a34;
    --green-deep: #0e6427;
    --green-band: #0b5a22;
    --green-strip: #2d9a3e;
    --ink-light: #ffffff;
    --headline-fill: #2aa23c;
    --produce-warm: #e0a23a;
    --produce-red: #c8352a;
    --produce-shade: #6b3a20;
  }
  * { box-sizing: border-box; margin: 0; padding: 0; }
  html, body {
    width: 1200px; height: 900px; overflow: hidden;
    background: var(--page);
  }
  .label {
    position: absolute; left: 6px; top: 6px;
    width: 1188px; height: 888px;
    border: 3px solid var(--frame);
    border-radius: 16px;
    overflow: hidden;
    background: radial-gradient(ellipse at 45% 40%, var(--green-bright) 0%, var(--green-mid) 55%, var(--green-deep) 100%);
  }
  .label__sheen {
    position: absolute; inset: 0; width: 100%; height: 100%;
  }
  .produce-photo {
    position: absolute; left: 195px; top: 232px;
    width: 830px; height: 520px;
    border-radius: 48% 48% 40% 40%;
    background:
      radial-gradient(ellipse at 50% 35%, var(--produce-warm) 0%, rgba(224,162,58,0.8) 30%, transparent 60%),
      radial-gradient(ellipse at 40% 70%, var(--produce-red) 0%, rgba(200,53,42,0.7) 35%, transparent 70%),
      radial-gradient(ellipse at 50% 50%, var(--produce-shade) 0%, rgba(107,58,32,0.4) 55%, transparent 72%);
  }
  .headline {
    position: absolute; left: 0; top: 0; width: 1188px; height: 888px;
  }
  .headline text {
    font-family: "Russo One", sans-serif;
    fill: var(--headline-fill);
    stroke: var(--ink-light);
    stroke-width: 5px;
    paint-order: stroke fill;
    letter-spacing: 2px;
  }
  .brand {
    position: absolute; right: 40px; top: 44px;
    width: 270px;
    display: flex; flex-direction: column; align-items: center; gap: 46px;
  }
  .brand__mark {
    width: 190px; height: 190px; border-radius: 50%;
    background: var(--green-deep);
  }
  .brand__name {
    font-family: "Russo One", sans-serif;
    font-size: 50px;
    line-height: 1;
    color: var(--green-deep);
  }
  .tagline-band {
    position: absolute; left: 0; right: 0; top: 830px; height: 40px;
    background: var(--green-band);
    display: flex; align-items: center; justify-content: center;
  }
  .tagline {
    font-family: "Cinzel", serif;
    font-weight: 700;
    font-size: 17px;
    letter-spacing: 1.5px;
    color: var(--ink-light);
  }
  .base-strip {
    position: absolute; left: 0; right: 0; top: 870px; bottom: 0;
    background: var(--green-strip);
  }
</style>
</head>
<body>
  <main class="label">
    <svg class="label__sheen" viewBox="0 0 1188 888" aria-hidden="true">
      <path d="M0 0 H640 C430 40 220 140 90 300 L0 300 Z" fill="#ffffff" opacity="0.06"/>
    </svg>

    <div class="produce-photo" role="img" aria-label="Wicker basket piled with fresh fruit: apples, orange, pear, bananas, grapes, strawberries, peaches, kiwi and watermelon"></div>

    <svg class="headline" viewBox="0 0 1188 888" role="heading" aria-level="1" aria-label="Keep Produce Fresher Longer">
      <defs>
        <path id="arc-top" d="M252 478 Q570 390 955 615"/>
        <path id="arc-bottom" d="M192 600 Q580 480 1000 705"/>
      </defs>
      <text font-size="64"><textPath href="#arc-top" textLength="740" lengthAdjust="spacingAndGlyphs">KEEP PRODUCE</textPath></text>
      <text font-size="72"><textPath href="#arc-bottom" textLength="850" lengthAdjust="spacingAndGlyphs">FRESHER LONGER</textPath></text>
    </svg>

    <div class="brand">
      <span class="brand__mark"></span>
      <span class="brand__name">SackPalo</span>
    </div>

    <div class="tagline-band">
      <p class="tagline">SEALED PACKETS FOR UP A 6 MONTH SUPPLY</p>
    </div>
    <div class="base-strip"></div>
  </main>
</body>
</html>
```